Moravel Aesthetic Doctor

I require an elegant, luxurious looking business card for my aesthetic business. I am a doctor and that will set me aside from competitors. I am planning to provide home and spa based treatments to clients with high expectations. I have attached my logo.

```html
<!DOCTYPE html>
<html lang="en">
<head>
<meta charset="utf-8">
<title>Moravel Aesthetic Doctor – Business Card</title>
<link rel="stylesheet" href="https://fonts.googleapis.com/css2?family=Roboto:wght@300;400;500&display=swap">
<style>
  :root {
    --backdrop: #3a3a3c;
    --card: #1f1f21;
    --card-front: #1b1b1d;
    --sky: #52b4e8;
    --silver: #a4abb8;
    --silver-soft: #7d828c;
    --text-light: #c9ccd2;
    --white: #ffffff;
  }
  * { margin: 0; padding: 0; box-sizing: border-box; }
  html, body {
    width: 799px; height: 1200px; overflow: hidden;
    background: var(--backdrop);
    font-family: "Roboto", Arial, sans-serif;
  }
  .canvas { position: relative; width: 799px; height: 1200px; }
  .card {
    position: absolute; left: 80px; width: 640px; height: 366px;
    border-radius: 4px; overflow: hidden;
    box-shadow: 0 14px 30px rgba(0,0,0,.45);
  }
  .card--front { top: 117px; background: var(--card-front); }
  .card--back { top: 717px; background: var(--card); }

  .front-mark {
    position: absolute; left: 50%; top: 50%;
    transform: translate(-50%, -50%);
    display: flex; align-items: center; gap: 18px;
  }
  .front-mark__circle {
    width: 150px; height: 150px; border-radius: 50%;
    border: 4px solid var(--silver-soft);
  }
  .front-mark__name {
    font-weight: 300; font-size: 40px; letter-spacing: 4px;
    color: var(--silver);
  }

  .card__waves { position: absolute; inset: 0; }

  .brand {
    position: absolute; left: 34px; top: 112px;
    display: flex; align-items: center; gap: 14px;
  }
  .brand__circle {
    width: 64px; height: 64px; border-radius: 50%;
    border: 3px solid var(--silver);
  }
  .brand__name {
    font-weight: 400; font-size: 30px; line-height: 1.05;
    letter-spacing: 2px; color: var(--text-light); text-transform: uppercase;
  }
  .brand__name span { display: block; font-size: 19px; letter-spacing: 3px; }

  .doctor { position: absolute; left: 40px; top: 200px; }
  .doctor__name { font-weight: 300; font-size: 21px; color: var(--text-light); }
  .doctor__post { font-size: 10px; font-style: italic; color: var(--sky); margin-top: 2px; }
  .doctor__diploma { font-size: 14px; color: var(--sky); line-height: 1.25; margin-top: 6px; }

  .tagline {
    position: absolute; right: 30px; top: 118px;
    text-align: right; font-size: 16px; line-height: 1.2; color: var(--white);
  }

  .contact {
    position: absolute; right: 30px; bottom: 26px;
    text-align: right; color: var(--text-light); font-size: 15px; line-height: 1.55;
  }
  .contact__row { display: flex; justify-content: flex-end; align-items: center; gap: 8px; }
  .contact__follow { margin-bottom: 6px; }
  .dot { width: 13px; height: 13px; border-radius: 50%; background: var(--sky); display: inline-block; }
  .contact svg { width: 14px; height: 14px; fill: var(--sky); }
</style>
</head>
<body>
<main class="canvas">

  <section class="card card--front" aria-label="Card front">
    <div class="front-mark">
      <div class="front-mark__circle"></div>
      <div class="front-mark__name">MORAVEL</div>
    </div>
  </section>

  <section class="card card--back" aria-label="Card back">
    <svg class="card__waves" viewBox="0 0 640 366" preserveAspectRatio="none">
      <path fill="var(--sky)" d="M0 0 H640 V205 C560 195 480 160 405 100 C330 45 250 24 0 22 Z"/>
      <path fill="none" stroke="var(--silver)" stroke-width="7" d="M0 38 C240 34 330 62 400 118 C480 180 565 215 640 222"/>
      <path fill="none" stroke="var(--silver)" stroke-width="3" d="M70 32 C200 28 290 38 350 64"/>
    </svg>

    <div class="brand">
      <div class="brand__circle"></div>
      <div class="brand__name">Moravel<span>Aesthetic Doctor</span></div>
    </div>

    <div class="doctor">
      <div class="doctor__name">Dr Elena Vorst</div>
      <div class="doctor__post">MRCPCH MD</div>
      <div class="doctor__diploma">Australasian Diploma of<br>Aesthetic Medicine</div>
    </div>

    <div class="tagline">Home and Spa<br>Based Treatments</div>

    <div class="contact">
      <div class="contact__row contact__follow">Follow us on: <span class="dot"></span><span class="dot"></span></div>
      <div class="contact__row">0800 555 014
        <svg viewBox="0 0 24 24"><path d="M6.6 10.8a15 15 0 0 0 6.6 6.6l2.2-2.2c.3-.3.7-.4 1-.2 1.1.4 2.3.6 3.6.6.6 0 1 .4 1 1V20c0 .6-.4 1-1 1C10.6 21 3 13.4 3 4c0-.6.4-1 1-1h3.5c.6 0 1 .4 1 1 0 1.3.2 2.5.6 3.6.1.3 0 .7-.2 1z"/></svg>
      </div>
      <div class="contact__row">elena@moravel.co.nz
        <svg viewBox="0 0 24 24"><path d="M2 5h20v14H2z M2 5l10 8 10-8" fill="none" stroke="var(--sky)" stroke-width="2"/></svg>
      </div>
      <div class="contact__row">www.moravel.co.nz
        <svg viewBox="0 0 24 24"><circle cx="12" cy="12" r="9" fill="none" stroke="var(--sky)" stroke-width="2"/><path d="M3 12h18M12 3c3 3 3 15 0 18M12 3c-3 3-3 15 0 18" fill="none" stroke="var(--sky)" stroke-width="1.6"/></svg>
      </div>
    </div>
  </section>

</main>
</body>
</html>
```